Business Card Design Project

Business Card
We are rebranding with a new logo
Industry/Entity Type
Business
Contact Information for Business Card
Dennis Morvale +61 487215963 dennis@quorv.com.au P.O. Box 872 Fernlow QLD 4309
Requirements
Must have
- Logo

```html
<!DOCTYPE html>
<html lang="en">
<head>
<meta charset="utf-8">
<title>Quorv International – Business Card</title>
<link rel="stylesheet" href="https://fonts.googleapis.com/css2?family=Roboto:wght@400;700&family=Yellowtail&display=swap">
<style>
  :root {
    --backdrop: #e4e4e4;
    --card: #f7f7f7;
    --ink: #222222;
    --brand-navy: #0d4f73;
    --brand-blue: #1a8fc4;
    --brand-orange: #d4561e;
    --white: #ffffff;
  }
  * { margin: 0; padding: 0; box-sizing: border-box; }
  html, body {
    width: 1200px; height: 576px; overflow: hidden;
    background: var(--backdrop);
    font-family: "Roboto", Arial, sans-serif;
  }
  .canvas { position: relative; width: 1200px; height: 576px; }
  .card {
    position: absolute; top: 138px;
    width: 484px; height: 294px;
    background: var(--card);
    border-radius: 12px;
    overflow: hidden;
  }
  .card--front { left: 82px; }
  .card--back { left: 602px; }

  .wordmark {
    color: var(--brand-navy);
    font-weight: 700;
    line-height: 1;
  }
  .wordmark__name { display: block; }
  .wordmark__tag { display: block; letter-spacing: 0.18em; }

  .card--front .wordmark {
    position: absolute; left: 0; right: 0; top: 92px;
    text-align: center;
  }
  .card--front .wordmark__name { font-size: 64px; }
  .card--front .wordmark__tag { font-size: 17px; margin-top: 14px; }

  .card--back .wordmark { position: absolute; left: 36px; top: 56px; }
  .card--back .wordmark__name { font-size: 50px; }
  .card--back .wordmark__tag { font-size: 13px; margin-top: 10px; }

  .contact { position: absolute; left: 234px; top: 142px; }
  .contact__name {
    font-family: "Yellowtail", cursive;
    font-size: 25px; color: var(--brand-navy);
    margin-bottom: 10px;
  }
  .contact__list { list-style: none; }
  .contact__item {
    display: flex; align-items: center;
    font-size: 12.5px; color: var(--ink);
    height: 17px;
  }
  .contact__icon { width: 12px; height: 12px; margin-right: 12px; fill: var(--brand-orange); }

  .band { position: absolute; left: 0; bottom: 0; width: 484px; height: 40px; }
  .website {
    position: absolute; left: 237px; bottom: 13px;
    font-size: 12.5px; color: var(--white);
  }
</style>
</head>
<body>
<main class="canvas">
  <section class="card card--front" aria-label="Card front">
    <div class="wordmark">
      <span class="wordmark__name">Quorv</span>
      <span class="wordmark__tag">INTERNATIONAL</span>
    </div>
  </section>

  <section class="card card--back" aria-label="Card back">
    <div class="wordmark">
      <span class="wordmark__name">Quorv</span>
      <span class="wordmark__tag">INTERNATIONAL</span>
    </div>

    <div class="contact">
      <p class="contact__name">Dennis Morvale</p>
      <ul class="contact__list">
        <li class="contact__item">
          <svg class="contact__icon" viewBox="0 0 24 24"><path d="M6.6 10.8a15 15 0 0 0 6.6 6.6l2.2-2.2c.3-.3.7-.4 1-.2 1.1.4 2.3.6 3.6.6.6 0 1 .4 1 1V20c0 .6-.4 1-1 1A17 17 0 0 1 3 4c0-.6.4-1 1-1h3.5c.6 0 1 .4 1 1 0 1.3.2 2.5.6 3.6.1.3 0 .7-.2 1z"/></svg>
          +61 487215963
        </li>
        <li class="contact__item">
          <svg class="contact__icon" viewBox="0 0 24 24"><path d="M2 5h20v14H2z M3 6l9 7 9-7" stroke="#f7f7f7" stroke-width="1.5"/></svg>
          dennis@quorv.com.au
        </li>
        <li class="contact__item">
          <svg class="contact__icon" viewBox="0 0 24 24"><path d="M12 2a7 7 0 0 0-7 7c0 5.2 7 13 7 13s7-7.8 7-13a7 7 0 0 0-7-7zm0 9.5A2.5 2.5 0 1 1 12 6.5a2.5 2.5 0 0 1 0 5z"/></svg>
          P.O. Box 872 Fernlow QLD 4309
        </li>
      </ul>
    </div>

    <svg class="band" viewBox="0 0 484 40" preserveAspectRatio="none">
      <defs>
        <linearGradient id="bandBlue" x1="0" x2="1">
          <stop offset="0" stop-color="#0d4f73"/>
          <stop offset="1" stop-color="#1a8fc4"/>
        </linearGradient>
      </defs>
      <rect x="0" y="22" width="210" height="18" fill="#d4561e"/>
      <polygon points="208,2 484,2 484,40 198,40" fill="url(#bandBlue)"/>
    </svg>
    <p class="website">www.quorv.com.au</p>
  </section>
</main>
</body>
</html>
```